Birchline Septic Solutions

Would like to see some single sided ones but would also like to see some double sided with one sided only being the logo. Owners name is Colin Vandro. Phone number is 555-214-0387
Services are pumping, inspections, installs, and repairs

Contact Information for Business Card

555-241-0387 Colin Vandro Cedar Ridge, OH

```html
<!DOCTYPE html>
<html lang="en">
<head>
<meta charset="UTF-8">
<title>Birchline Septic Solutions — Business Cards</title>
<link href="https://fonts.googleapis.com/css2?family=Roboto:wght@400;700&display=swap" rel="stylesheet">
<style>
  :root {
    --backdrop: #3b3b3b;
    --card: #161616;
    --teal: #2fb8b3;
    --white: #f2f2f2;
    --muted: #d6d6d6;
    --steel: #8a8a8a;
  }
  * { margin: 0; padding: 0; box-sizing: border-box; }
  html, body {
    width: 1200px; height: 801px; overflow: hidden;
    background: var(--backdrop);
    font-family: "Roboto", Arial, sans-serif;
  }
  .stage {
    width: 1200px; height: 801px;
    display: flex; align-items: center; justify-content: center; gap: 24px;
  }
  .card {
    width: 540px; height: 309px;
    background: var(--card);
    border-bottom: 3px solid var(--teal);
    position: relative;
    display: flex;
  }
  /* contact side */
  .card-front .brand-block {
    width: 52%;
    display: flex; align-items: center; justify-content: center;
    padding-left: 22px;
  }
  .brand-name {
    font-weight: 700; color: var(--white);
    font-size: 24px; line-height: 1.15; text-transform: uppercase;
    letter-spacing: 1px;
  }
  .brand-name .sub { display: block; }
  .divider {
    width: 1px; background: var(--teal);
    margin: 70px 0;
  }
  .contact-block {
    flex: 1; padding: 0 0 0 20px;
    display: flex; flex-direction: column; justify-content: center;
  }
  .person-name {
    color: var(--teal); font-weight: 700; font-size: 19px; letter-spacing: 0.3px;
  }
  .person-title { color: var(--muted); font-size: 13px; margin: 2px 0 14px; }
  .contact-list { list-style: none; }
  .contact-list li {
    display: flex; align-items: center; gap: 8px;
    color: var(--white); font-size: 13px; line-height: 1.65;
  }
  .contact-list svg { width: 11px; height: 11px; fill: var(--teal); flex: none; }
  /* logo side */
  .card-back { align-items: center; justify-content: center; }
  .card-back .brand-name {
    color: var(--steel); font-size: 38px; text-align: center; letter-spacing: 2px;
  }
</style>
</head>
<body>
<main class="stage">
  <section class="card card-front" aria-label="Business card, contact side">
    <div class="brand-block">
      <p class="brand-name">Birchline<span class="sub">Septic Solutions</span></p>
    </div>
    <div class="divider"></div>
    <div class="contact-block">
      <p class="person-name">COLIN VANDRO</p>
      <p class="person-title">Founder / CEO</p>
      <ul class="contact-list">
        <li><svg viewBox="0 0 24 24" aria-hidden="true"><path d="M6.6 10.8a15.5 15.5 0 0 0 6.6 6.6l2.2-2.2c.3-.3.7-.4 1-.2 1.1.4 2.3.6 3.6.6.6 0 1 .4 1 1V20c0 .6-.4 1-1 1A17 17 0 0 1 3 4c0-.6.4-1 1-1h3.5c.6 0 1 .4 1 1 0 1.3.2 2.5.6 3.6.1.3 0 .7-.2 1z"/></svg>555-241-0387</li>
        <li><svg viewBox="0 0 24 24" aria-hidden="true"><path d="M2 5h20v14H2zM4 7v.5l8 5 8-5V7l-8 5z"/></svg>info@birchlineseptic.com</li>
        <li><svg viewBox="0 0 24 24" aria-hidden="true"><circle cx="12" cy="12" r="10"/></svg>www.birchlineseptic.com</li>
        <li><svg viewBox="0 0 24 24" aria-hidden="true"><path d="M12 2a7 7 0 0 0-7 7c0 5 7 13 7 13s7-8 7-13a7 7 0 0 0-7-7zm0 9.5A2.5 2.5 0 1 1 12 6.5a2.5 2.5 0 0 1 0 5z"/></svg>Cedar Ridge, OH</li>
      </ul>
    </div>
  </section>

  <section class="card card-back" aria-label="Business card, logo side">
    <p class="brand-name">Birchline<span class="sub">Septic Solutions</span></p>
  </section>
</main>
</body>
</html>
```